KBT Business Cards

We require business cards for our business. We would like a matte black back to the card, with our logo centred in the middle. The front side of the card is open to design.

Target Market(s)

Clients looking for legal services (professional)

Industry/Entity Type

Legal

Contact Information for Business Card

Doran Kelbrath
Partner
Mobile: 0461 738 524
Email: doran@kbtlaw.co
Website: www.kbtlaw.co
Level 3, 118 Wendmore Street
Sydney NSW 2000

Font styles to use
Other font styles liked:
• Avenir

Colors
f04a50
ffffff
1b1b1b

Requirements
Must have
• Black back with logo included in the centre of the card.
• Our font is Avenir.

```html
<!DOCTYPE html>
<html lang="en">
<head>
<meta charset="utf-8">
<title>KBT Business Cards</title>
<link rel="stylesheet" href="https://fonts.googleapis.com/css2?family=Nunito+Sans:wght@400;600;800&display=swap">
<style>
  :root {
    --stage: #3a3a3a;
    --ink: #1b1b1b;
    --paper: #ffffff;
    --accent: #c21f4b;
    --muted: #2a2a2a;
  }
  * { margin: 0; padding: 0; box-sizing: border-box; }
  html, body { width: 1200px; height: 900px; overflow: hidden; }
  body {
    background: var(--stage);
    font-family: "Nunito Sans", Arial, sans-serif;
    color: var(--ink);
    position: relative;
  }
  .card {
    position: absolute;
    left: 280px;
    width: 640px;
    height: 366px;
    overflow: hidden;
  }
  .card-back { top: 60px; background: var(--ink); }
  .card-front { top: 474px; background: var(--paper); }

  .back-texture {
    position: absolute; inset: 0;
    background: radial-gradient(ellipse at 70% 40%, #3c3c3c 0%, var(--ink) 70%);
  }
  .firm-mark {
    position: absolute;
    display: flex; align-items: center; gap: 22px;
  }
  .firm-mark .mark-square { width: 70px; height: 70px; background: var(--accent); flex: none; }
  .firm-name {
    font-weight: 800;
    text-transform: uppercase;
    line-height: 1.02;
  }
  .card-back .firm-mark { left: 50%; top: 50%; transform: translate(-50%, -50%); }
  .card-back .firm-name { color: var(--paper); font-size: 34px; }

  .contact { position: absolute; left: 42px; top: 58px; }
  .person-name {
    color: var(--accent);
    font-weight: 800;
    font-size: 25px;
    letter-spacing: 0.5px;
    text-transform: uppercase;
  }
  .person-role { font-size: 15px; margin-bottom: 14px; }
  .contact-list { list-style: none; font-size: 16px; }
  .contact-list li { display: flex; align-items: center; gap: 12px; height: 25px; }
  .contact-list svg { width: 16px; height: 16px; fill: var(--accent); flex: none; }
  .address { margin-top: 12px; font-size: 16px; line-height: 1.5; }

  .card-front .firm-mark { left: 372px; top: 150px; gap: 18px; }
  .card-front .mark-square { width: 56px; height: 56px; }
  .card-front .firm-name { color: var(--ink); font-size: 25px; }

  .footer-band {
    position: absolute; left: 0; right: 0; bottom: 0; height: 34px;
    background: linear-gradient(90deg, #0e0e0e 0%, #5a1a2b 50%, var(--accent) 100%);
  }
</style>
</head>
<body>
  <section class="card card-back" aria-label="Card back">
    <div class="back-texture" role="img" aria-label="Dark diamond texture background"></div>
    <div class="firm-mark">
      <span class="mark-square"></span>
      <div class="firm-name">Kelbrath<br>Brenner<br>Tate</div>
    </div>
  </section>

  <section class="card card-front" aria-label="Card front">
    <div class="contact">
      <h1 class="person-name">Doran Kelbrath</h1>
      <p class="person-role">Partner</p>
      <ul class="contact-list">
        <li>
          <svg viewBox="0 0 16 16"><path d="M3.2 1.2l2.4 0 1.2 3.2-1.6 1.2c.8 1.8 2.4 3.4 4.2 4.2l1.2-1.6 3.2 1.2 0 2.4c0 .9-.8 1.6-1.7 1.5C6.2 12.9 2.6 9.3 1.7 3c-.1-.9.6-1.8 1.5-1.8z"/></svg>
          0461 738 524
        </li>
        <li>
          <svg viewBox="0 0 16 16"><path d="M1 3h14v10H1z M2 4.2v.4l6 4 6-4v-.4z" fill-rule="evenodd"/></svg>
          doran@kbtlaw.co
        </li>
        <li>
          <svg viewBox="0 0 16 16"><path d="M8 1a7 7 0 1 0 0 14A7 7 0 0 0 8 1zm0 1.5c.8 0 1.6 1.6 1.9 4.5H6.1C6.4 4.1 7.2 2.5 8 2.5zM6.1 8.5h3.8c-.3 2.9-1.1 4.5-1.9 4.5s-1.6-1.6-1.9-4.5zM2.6 8.5h2c.1 1.6.4 3 .9 4a5.5 5.5 0 0 1-2.9-4zm0-1.5a5.5 5.5 0 0 1 2.9-4c-.5 1-.8 2.4-.9 4zm8.8 0c-.1-1.6-.4-3-.9-4a5.5 5.5 0 0 1 2.9 4zm0 1.5h2a5.5 5.5 0 0 1-2.9 4c.5-1 .8-2.4.9-4z"/></svg>
          www.kbtlaw.co
        </li>
      </ul>
      <p class="address">Level 3, 118 Wendmore Street<br>Sydney NSW 2000</p>
    </div>

    <div class="firm-mark">
      <span class="mark-square"></span>
      <div class="firm-name">Kelbrath<br>Brenner<br>Tate</div>
    </div>

    <div class="footer-band" role="img" aria-label="Decorative band of squares fading from black to crimson"></div>
  </section>
</body>
</html>
```